Landscape design build company door flyer

I would like this flyer to convey a high-level of professionalism for a company that is excellent with communication with their clients as well as a company that does incredible installations

Went on vacation/holiday

```html
<!DOCTYPE html>
<html lang="en">
<head>
<meta charset="utf-8">
<title>Stillwater Builders – Door Hanger</title>
<link href="https://fonts.googleapis.com/css2?family=Playfair+Display:wght@700;800;900&family=Lato:wght@400;700;900&display=swap" rel="stylesheet">
<style>
  :root {
    --navy: #0f2a3d;
    --navy-deep: #0b2131;
    --gold: #ffb800;
    --gold-soft: #ffc21f;
    --paper: #eeeff0;
    --paper-shade: #e3e5e7;
    --ink: #1d2f3e;
    --stage: #cdd6e0;
  }
  * { box-sizing: border-box; margin: 0; padding: 0; }
  html, body { width: 1200px; height: 673px; overflow: hidden; }
  body {
    background: var(--stage);
    position: relative;
    font-family: "Lato", Arial, sans-serif;
    color: var(--ink);
  }
  .hanger {
    position: absolute;
    top: 29px;
    width: 458px;
    height: 1183px;
    transform: scale(0.52);
    transform-origin: top left;
    background: radial-gradient(ellipse at 40% 30%, var(--paper) 0%, var(--paper-shade) 100%);
    overflow: hidden;
  }
  .hanger--front { left: 332px; }
  .hanger--back { left: 630px; }

  /* front */
  .front-photo {
    position: absolute; left: 0; right: 0; top: 700px; bottom: 0;
    background: linear-gradient(180deg, rgba(238,239,240,0) 0%, #c9cdd0 18%, #b9c3b0 42%, #6f8a5c 58%, #dfe3e6 74%, #9aa6b2 100%);
  }
  .brand { position: absolute; top: 300px; left: 0; right: 0; text-align: center; }
  .brand__mark {
    width: 88px; height: 88px; border-radius: 50%;
    background: var(--navy); margin: 0 auto 40px;
  }
  .brand__name {
    font-family: "Playfair Display", Georgia, serif; font-weight: 700;
    font-size: 31px; color: var(--navy); letter-spacing: 0.5px; line-height: 1;
  }
  .brand__tagline {
    font-weight: 700; font-size: 14px; color: var(--navy); letter-spacing: 0.3px; margin-top: 4px;
  }
  .rule { position: absolute; top: 488px; left: 70px; right: 70px; height: 1px; background: #9aa6b0; }
  .headline { position: absolute; top: 502px; left: 0; right: 0; text-align: center; font-family: "Playfair Display", Georgia, serif; color: var(--navy-deep); }
  .headline__lead { font-weight: 800; font-size: 31px; line-height: 1.1; letter-spacing: -0.3px; }
  .headline__main { font-weight: 900; font-size: 72px; line-height: 0.95; letter-spacing: -1px; }
  .promise {
    position: absolute; top: 611px; left: 50px; width: 358px; height: 66px;
    background: var(--gold); border-radius: 6px;
    font-size: 23px; line-height: 1.1; color: var(--navy); text-align: center;
    padding-top: 8px; letter-spacing: -0.4px;
  }
  .cta-box {
    position: absolute; top: 686px; left: 113px; width: 295px; height: 84px;
    background: var(--navy); border-radius: 6px; color: #fff;
    font-weight: 700; font-size: 33px; line-height: 0.9; letter-spacing: -0.8px;
    padding: 12px 0 0 22px;
  }

  /* back */
  .services-title {
    position: absolute; top: 309px; left: 94px; width: 270px; height: 62px;
    background: var(--navy); border-radius: 6px; color: var(--gold);
    font-family: "Playfair Display", Georgia, serif; font-weight: 700;
    font-size: 46px; text-align: center; line-height: 62px; letter-spacing: 0.5px;
  }
  .intro {
    position: absolute; top: 391px; left: 48px; right: 48px; text-align: center;
    font-size: 14px; line-height: 18px; color: var(--navy); letter-spacing: -0.3px;
  }
  .service-grid {
    position: absolute; top: 538px; left: 40px; width: 380px; height: 195px;
    display: grid; grid-template-columns: 1fr 1fr; row-gap: 28px; column-gap: 28px;
  }
  .service-grid::after {
    content: ""; position: absolute; left: 190px; top: 20px; bottom: 10px; width: 1px; background: #9aa6b0;
  }
  .service { display: flex; align-items: center; gap: 16px; font-size: 20px; line-height: 1.08; color: var(--navy); }
  .service__icon { width: 40px; height: 36px; flex: none; display: block; }
  .back-photo {
    position: absolute; top: 763px; left: 0; right: 0; height: 284px;
    border-top: 5px solid var(--navy);
    background: linear-gradient(180deg, #6fa2d8 0%, #b6d2ea 28%, #7d9b5e 48%, #b08a5c 62%, #c7ced6 80%, #8f9aa6 100%);
  }
  .estimate-band {
    position: absolute; top: 1047px; left: 0; right: 0; height: 55px;
    background: var(--navy); color: #fff; text-align: center;
    font-weight: 700; font-size: 24px; line-height: 55px; letter-spacing: -0.6px;
  }
  .phone-band {
    position: absolute; top: 1102px; left: 0; right: 0; bottom: 0;
    background: var(--gold); color: var(--navy);
    display: flex; align-items: center; justify-content: center; gap: 16px;
    font-weight: 900; font-size: 40px; letter-spacing: -0.5px;
  }
  .phone-band svg { width: 34px; height: 34px; }
</style>
</head>
<body>

<section class="hanger hanger--front" aria-label="Door hanger front">
  <div class="front-photo" role="img" aria-label="Modern backyard with pergola, reflecting pool, stone pavers and lush plants"></div>
  <div class="brand">
    <div class="brand__mark"></div>
    <div class="brand__name">STILLWATER BUILDERS</div>
    <div class="brand__tagline">OUTDOOR LIVING SPACES</div>
  </div>
  <div class="rule"></div>
  <div class="headline">
    <div class="headline__lead">IT’S TIME TO DISCOVER</div>
    <div class="headline__main">YOUR ZEN!</div>
  </div>
  <div class="promise">From vision to reality, let us bring<br>your dream outdoor space to life</div>
  <div class="cta-box">GET A FAST FREE<br>ESTIMATE NOW!</div>
</section>

<section class="hanger hanger--back" aria-label="Door hanger back">
  <div class="services-title">SERVICES</div>
  <p class="intro">Our team of skilled artisans will turn your outdoor space into a breathtaking oasis that you’ll love coming home to. Whether it’s a cozy patio for intimate gatherings, a sprawling deck to host memorable parties, or a custom paver driveway that adds instant curb appeal, our high-quality craftsmanship ensures stunning results that exceed your expectations.</p>
  <div class="service-grid">
    <div class="service"><svg class="service__icon" viewBox="0 0 40 36"><rect x="4" y="4" width="32" height="28" rx="3" fill="#0f2a3d"/></svg>Paver Patios<br>&amp; Pools</div>
    <div class="service"><svg class="service__icon" viewBox="0 0 40 36"><rect x="4" y="4" width="32" height="28" rx="3" fill="#0f2a3d"/></svg>Decks &amp;<br>Railings</div>
    <div class="service"><svg class="service__icon" viewBox="0 0 40 36"><rect x="4" y="4" width="32" height="28" rx="3" fill="#0f2a3d"/></svg>Paver<br>Driveways</div>
    <div class="service"><svg class="service__icon" viewBox="0 0 40 36"><rect x="4" y="4" width="32" height="28" rx="3" fill="#0f2a3d"/></svg>Fireplace<br>&amp; Firepits</div>
    <div class="service"><svg class="service__icon" viewBox="0 0 40 36"><rect x="4" y="4" width="32" height="28" rx="3" fill="#0f2a3d"/></svg>Retaining<br>Walls</div>
    <div class="service"><svg class="service__icon" viewBox="0 0 40 36"><rect x="4" y="4" width="32" height="28" rx="3" fill="#0f2a3d"/></svg>Outdoor<br>Lighting</div>
  </div>
  <div class="back-photo" role="img" aria-label="Sunny backyard with wooden pergola, outdoor lounge seating, dining set and palm trees"></div>
  <div class="estimate-band">GET A FAST FREE ESTIMATE NOW!</div>
  <div class="phone-band">
    <svg viewBox="0 0 24 24" aria-hidden="true"><path fill="#0f2a3d" d="M6.6 10.8a15.1 15.1 0 0 0 6.6 6.6l2.2-2.2c.3-.3.7-.4 1-.2 1.1.4 2.3.6 3.6.6.6 0 1 .4 1 1V20c0 .6-.4 1-1 1C10.6 21 3 13.4 3 4c0-.6.4-1 1-1h3.5c.6 0 1 .4 1 1 0 1.3.2 2.5.6 3.6.1.3 0 .7-.2 1z"/></svg>
    <span>555 204 8816</span>
  </div>
</section>

</body>
</html>
```